Web Design for Webdesign company 3 page PSD

Project
---------
We need a PSD Web Design to be used in a WordPress installation.
What we would like to create is a professional looking website for a web design agency. We also need you to look for suitable stock images to be placed on these pages.
We need the design for:
Homepage
Landing page
Contact page
attached in the pages file you will find a file with more in depth details how these files should be build up.
We would like to see a desktop version and a mobile version of these pages
The website should have a 1100px width.
The mobile design should have 480px width.
The homepage should have a header slider about 450px high.
The slider is preferred full width and should have some images text and a button
Objectives
-------------
The main objective for the website is to get leads from customers in the form of a request for a quotation or a call or mail me back action. The most important action for the homepage is to link and navigate to our landing pages.
What we want to tell our visitors (our main products)
-------------------------------------------------------------------
- A website with no big investment but a monthly rate
- A successful website with no worries (a complete website, seo, hosting and a service contract for future customization is included for a monthly rate)
Color Scheme
------------
Use branding colors. You can find them in the branding.pdf file.
Additional colors:
White: #ffffff
Black: #181818
Company info
--------------
We are a starting web design / marketing agency based in The Netherlands and looking for the design of our website. Our services are (custom) webdesign, website marketing or combinations of both. Our main customer group is small business owners.
We sell websites but give the option to buy it with a lease contract.
A second product is a default website with a complete service: SEO, hosting and a service contract for a monthly rate.
Content:
-----------
If not available place Lorem Ipsum text.
There will come about 400 words of text on the landing pages
Design Competition
--------------------------
Since this is a designing competition we would like to see your creativity.
What you can expect from us is a lot of feedback 7 days a week with short response time.
You can send us the first sketchy mock ups of the homepage and we will give feedback based on these design. But we like your feedback or comments as well
Read the pages file for more in depth details how the pages should be designed

Target Market(s)
Small business owners in The Netherlands
Industry/Entity Type
It Company
Number of Pages Required
3 page
Requirements
Must have
- Homepage:
- Header slider with images, some text and a link to a custom page
- The slider should have 3 designed slides
- Landings page:
- Sidebar
- Action button for a request for a quotation
- Action button for a call me back action
- Action button for an appointment
- Contact form:
- Address details
- Contact form
Nice to have
- Homepage:
- Full width slider
- Testimonial block
- Blog items
Should not have
- Flash
- A to crowded design

```html
<!DOCTYPE html>
<html lang="en">
<head>
<meta charset="utf-8">
<title>Quiet Oak Internet Services</title>
<link href="https://fonts.googleapis.com/css2?family=Play:wght@400;700&family=Arimo:wght@400;700&display=swap" rel="stylesheet">
<style>
:root{
  --teal:#337684;
  --teal-dark:#2c6874;
  --green:#5b9a78;
  --ink:#181818;
  --text:#444444;
  --muted:#666666;
  --light:#f4f4f4;
  --band:#ececec;
  --line:#e2e2e2;
  --white:#ffffff;
}
*{margin:0;padding:0;box-sizing:border-box}
html,body{width:1192px;height:1200px;overflow:hidden;background:var(--white)}
body{font-family:'Arimo',Arial,sans-serif;color:var(--text);position:relative}
.heading{font-family:'Play',sans-serif}

.topbar{height:44px;background:var(--light);border-bottom:1px solid var(--line);position:relative}
.topbar .contact-item{position:absolute;top:0;height:44px;display:flex;align-items:center;gap:10px;font-size:12px;font-weight:700;color:#8a8a8a;padding:0 18px;border-right:1px solid var(--line)}
.topbar .phone{left:80px}
.topbar .mail{left:222px}
.socials{position:absolute;right:76px;top:0;display:flex;height:44px}
.socials span{width:54px;height:44px;border-left:1px solid var(--line);display:flex;align-items:center;justify-content:center}
.socials span:last-child{border-right:1px solid var(--line)}
.socials i{width:10px;height:10px;border:1.5px solid #9a9a9a;border-radius:50%;display:block}

.site-header{height:91px;position:relative;background:var(--white)}
.brand{position:absolute;left:78px;top:22px;display:flex;align-items:center;gap:12px}
.brand-mark{width:44px;height:44px;border-radius:50%;background:var(--teal)}
.brand-name{font-family:'Play',sans-serif;font-weight:700;font-size:19px;line-height:19px;color:var(--teal)}
.main-nav{position:absolute;right:80px;top:0;height:91px;display:flex;align-items:center;gap:38px;font-family:'Play',sans-serif;font-size:15px;color:#333}
.main-nav a{text-decoration:none;color:inherit}
.main-nav a.active{color:var(--teal)}

.hero{height:465px;position:relative;overflow:hidden}
.hero-photo{position:absolute;inset:0;background:linear-gradient(100deg,#d9e2ea 0%,#aeb8c2 22%,#cfd7df 40%,#e6c6ad 58%,#b8cde4 75%,#e4e9ee 100%)}
.hero-caption{position:absolute;left:107px;top:119px;width:402px;height:293px;background:rgba(40,40,40,.72)}
.hero-caption .title{height:106px;background:#2a2a2a;border-bottom:2px solid var(--green);color:var(--white);font-size:30px;line-height:41px;text-align:center;padding-top:11px}
.hero-caption p{color:var(--white);font-size:18px;line-height:23px;text-align:center;padding:18px 28px 0}
.btn-pill{position:absolute;left:115px;top:219px;width:168px;height:48px;border-radius:24px;background:var(--teal);color:var(--white);font-family:'Play',sans-serif;font-weight:700;font-size:15px;display:flex;align-items:center;justify-content:center}
.hero-arrow{position:absolute;top:218px}
.hero-arrow.prev{left:38px}
.hero-arrow.next{right:48px}

.intro{height:135px;position:relative;background:var(--white)}
.icon-ring{position:absolute;border:1.5px solid var(--teal);border-radius:50%;display:flex;align-items:center;justify-content:center}
.intro .icon-ring{left:88px;top:32px;width:72px;height:72px}
.intro h2{position:absolute;left:192px;top:30px;font-weight:400;font-size:29px;color:#555}
.accent{color:var(--green)}
.intro p{position:absolute;left:193px;top:76px;font-size:14px;color:#555}
.btn-outline{position:absolute;left:892px;top:39px;width:186px;height:50px;border:1.5px solid var(--teal);border-radius:25px;font-family:'Play',sans-serif;font-size:18px;color:var(--teal);display:flex;align-items:center;justify-content:center}

.welcome{height:289px;background:var(--band);position:relative}
.devices{position:absolute;left:109px;top:41px;width:362px;height:202px;background:linear-gradient(180deg,#d8dde2 0%,#f3d4b8 45%,#c9ced3 100%);border-radius:6px}
.welcome .icon-ring{left:531px;top:52px;width:62px;height:62px;border:2px solid #555}
.welcome h2{position:absolute;left:601px;top:58px;font-weight:400;font-size:36px;color:#333}
.welcome p{position:absolute;left:528px;top:126px;width:556px;font-size:13px;line-height:26px;color:#555}

.site-footer{height:125px;background:var(--teal);position:relative;color:var(--white)}
.footer-ring{position:absolute;top:24px;width:72px;height:72px;border-radius:50%;border:2px solid var(--white);display:flex;align-items:center;justify-content:center}
.footer-ring .core{width:60px;height:60px;border-radius:50%;background:var(--white);display:flex;align-items:center;justify-content:center}
.footer-ring.home{left:83px}
.footer-ring.call{left:452px}
.footer-block{position:absolute;font-size:15px;line-height:22px}
.footer-block.address{left:170px;top:27px}
.footer-block.address h3{font-family:'Play',sans-serif;font-weight:400;font-size:18px;margin-bottom:7px}
.footer-block.reach{left:551px;top:37px;line-height:32px}
.search{position:absolute;left:806px;top:39px;width:310px;height:46px;border:1px solid var(--white);display:flex;align-items:center;justify-content:space-between;padding:0 12px;font-size:15px}
.copyright{height:51px;background:var(--teal);border-top:1px solid #5a95a1;color:var(--white);font-size:13px;display:flex;align-items:center;justify-content:center}
.copyright u{margin-left:4px}
</style>
</head>
<body>

<div class="topbar">
  <div class="contact-item phone">
    <svg width="12" height="12" viewBox="0 0 24 24"><path fill="#8a8a8a" d="M6.6 10.8a15 15 0 0 0 6.6 6.6l2.2-2.2a1 1 0 0 1 1-.25 11.4 11.4 0 0 0 3.6.57 1 1 0 0 1 1 1V20a1 1 0 0 1-1 1A17 17 0 0 1 3 4a1 1 0 0 1 1-1h3.5a1 1 0 0 1 1 1c0 1.25.2 2.45.57 3.57a1 1 0 0 1-.25 1z"/></svg>
    + 123 555 0199
  </div>
  <div class="contact-item mail">
    <svg width="13" height="10" viewBox="0 0 26 20"><path fill="#8a8a8a" d="M0 0h26v3L13 11 0 3zM0 6l13 8 13-8v14H0z"/></svg>
    info@quietoak.com
  </div>
  <div class="socials"><span><i></i></span><span><i></i></span><span><i></i></span><span><i></i></span><span><i></i></span></div>
</div>

<header class="site-header">
  <div class="brand">
    <div class="brand-mark"></div>
    <div class="brand-name">QUIET OAK<br>INTERNET SERVICES</div>
  </div>
  <nav class="main-nav">
    <a class="active">Home</a><a>About</a><a>Web design</a><a>Services</a><a>Contact</a>
  </nav>
</header>

<section class="hero">
  <div class="hero-photo" role="img" aria-label="Photo of two smiling colleagues working at a computer in a bright office"></div>
  <div class="hero-caption">
    <div class="title heading">A website from €19,95<br>per month</div>
    <p>With us, you can lease a website. So no big investment upfront. A website is available from € 19.95 per month</p>
    <div class="btn-pill">More Information</div>
  </div>
  <svg class="hero-arrow prev" width="18" height="30" viewBox="0 0 18 30"><path d="M15 3 4 15l11 12" fill="none" stroke="#fff" stroke-width="3"/></svg>
  <svg class="hero-arrow next" width="18" height="30" viewBox="0 0 18 30"><path d="M3 3l11 12L3 27" fill="none" stroke="#fff" stroke-width="3"/></svg>
</section>

<section class="intro">
  <div class="icon-ring"><svg width="24" height="24" viewBox="0 0 24 24"><circle cx="12" cy="12" r="10" fill="var(--green)"/></svg></div>
  <h2 class="heading">We Create <span class="accent">Awesome</span> Designs</h2>
  <p>Lorem Ipsum is simply dummy text of the printing and typesetting industry.</p>
  <div class="btn-outline">Web Design</div>
</section>

<section class="welcome">
  <div class="devices" role="img" aria-label="Illustration of a responsive website shown on desktop, laptop, tablet and phone screens"></div>
  <div class="icon-ring"><svg width="50" height="50" viewBox="0 0 50 50"><circle cx="25" cy="25" r="24" fill="#555"/><circle cx="25" cy="25" r="9" fill="#fff"/></svg></div>
  <h2 class="heading">Welcome to <span class="accent">QUIET OAK</span></h2>
  <p>Lorem Ipsum is simply dummy text of the printing and typesetting industry. Lorem Ipsum has been the industry's standard dummy text ever since the 1500s, when an unknown printer took a galley of type and scrambled it to make a type specimen book. It has survived not only five centuries, but also the leap</p>
</section>

<footer class="site-footer">
  <div class="footer-ring home"><div class="core">
    <svg width="30" height="28" viewBox="0 0 30 28"><path fill="var(--teal)" d="M15 2 1 14h4v12h7v-8h6v8h7V14h4z"/></svg>
  </div></div>
  <div class="footer-block address">
    <h3>Quiet Oak Internet Services</h3>
    254, Office area name,<br>City, State, Country
  </div>
  <div class="footer-ring call"><div class="core">
    <svg width="26" height="26" viewBox="0 0 24 24"><path fill="var(--teal)" d="M6.6 10.8a15 15 0 0 0 6.6 6.6l2.2-2.2a1 1 0 0 1 1-.25 11.4 11.4 0 0 0 3.6.57 1 1 0 0 1 1 1V20a1 1 0 0 1-1 1A17 17 0 0 1 3 4a1 1 0 0 1 1-1h3.5a1 1 0 0 1 1 1c0 1.25.2 2.45.57 3.57a1 1 0 0 1-.25 1z"/></svg>
  </div></div>
  <div class="footer-block reach">
    Phone No. : + 123 555 0199<br>Email : info@quietoak.com
  </div>
  <div class="search">
    Search...
    <svg width="20" height="20" viewBox="0 0 20 20"><circle cx="8" cy="8" r="6" fill="none" stroke="var(--green)" stroke-width="2.5"/><path d="M12.5 12.5 18 18" stroke="var(--green)" stroke-width="2.5"/></svg>
  </div>
</footer>
<div class="copyright">© 2015 <u>Quiet Oak</u>. All Rights Reserved.</div>

</body>
</html>
```